Bramble firearms training and consulting

Business card for a new firearms training company. I train persons on firearms safety, personal protection, shooting tactics and CHL.Im a Prior State trooper. I also served 4 years in IRaq as a Protection contractor with the Dept of State. Real world training for Real world situations. I would like the company name to be, BRAMBLE FIREARMS TRAINING AND CONSULTING. Im native american also. Ive provided pics. Put the name Bramble above the arrowhead but rotate the arrowhead to the right with it pointing right. Then place bramble inside the arrowhead. lets see both.
Industry/Entity Type
Business
Contact Information for Business Card
Christian Chatellier817-240-0488shadowtraining33@gmail.com

```html
<!DOCTYPE html>
<html lang="en">
<head>
<meta charset="utf-8">
<title>Bramble Firearms – Business Card</title>
<link href="https://fonts.googleapis.com/css2?family=Cinzel:wght@400;700&family=Raleway:wght@400;500&display=swap" rel="stylesheet">
<style>
  :root {
    --page-bg: #151515;
    --card-bg: #2e3036;
    --brand-red: #c1161c;
    --name-red: #d8242a;
    --text-light: #e4e4e6;
    --text-muted: #b9babd;
    --tagline-grey: #8c8d91;
  }
  html, body {
    margin: 0;
    width: 1200px;
    height: 900px;
    overflow: hidden;
    background: var(--page-bg);
  }
  .stage { position: relative; width: 1200px; height: 900px; }
  .card {
    position: absolute;
    left: 331px;
    width: 547px;
    height: 318px;
    border-radius: 18px;
    background: var(--card-bg);
  }
  .card--front { top: 118px; }
  .card--back { top: 487px; }

  .brand { position: absolute; text-align: center; }
  .brand__mark {
    display: block;
    margin: 0 auto;
    border-radius: 50%;
    background: var(--brand-red);
  }
  .brand__name {
    font-family: "Cinzel", serif;
    font-weight: 700;
    color: var(--brand-red);
    white-space: nowrap;
    letter-spacing: 0.02em;
  }
  .brand__tagline {
    display: flex;
    align-items: center;
    justify-content: center;
    gap: 8px;
    font-family: "Cinzel", serif;
    font-weight: 400;
    color: var(--tagline-grey);
    white-space: nowrap;
  }
  .brand__tagline::before,
  .brand__tagline::after {
    content: "";
    height: 1px;
    background: var(--tagline-grey);
  }

  .card--front .brand { left: 28px; top: 106px; width: 248px; }
  .card--front .brand__mark { width: 44px; height: 44px; margin-bottom: 24px; }
  .card--front .brand__name { font-size: 20px; line-height: 24px; }
  .card--front .brand__tagline { font-size: 11px; line-height: 16px; }
  .card--front .brand__tagline::before,
  .card--front .brand__tagline::after { width: 22px; }

  .contact {
    position: absolute;
    left: 286px;
    top: 114px;
    font-family: "Raleway", sans-serif;
  }
  .contact__name { margin: 0; font-size: 26px; font-weight: 400; line-height: 32px; color: var(--name-red); }
  .contact__role { margin: 0 0 26px 2px; font-size: 16px; line-height: 20px; color: var(--text-muted); }
  .contact__line { margin: 0 0 0 4px; font-size: 15px; line-height: 19px; color: var(--text-light); }

  .card--back .brand { left: 0; top: 98px; width: 547px; }
  .card--back .brand__mark { width: 62px; height: 62px; margin-bottom: 42px; }
  .card--back .brand__name { font-size: 28px; line-height: 32px; }
  .card--back .brand__tagline { font-size: 15px; line-height: 22px; gap: 10px; }
  .card--back .brand__tagline::before,
  .card--back .brand__tagline::after { width: 30px; }
</style>
</head>
<body>
  <main class="stage">
    <section class="card card--front" aria-label="Business card front">
      <div class="brand">
        <span class="brand__mark" aria-hidden="true"></span>
        <div class="brand__name">BRAMBLE FIREARMS</div>
        <div class="brand__tagline">TRAINING AND CONSULTING</div>
      </div>
      <div class="contact">
        <h1 class="contact__name">Dorian Pellwick</h1>
        <p class="contact__role">Managing Director</p>
        <p class="contact__line">info@bramblerange.com</p>
        <p class="contact__line">044-987 654 321</p>
      </div>
    </section>

    <section class="card card--back" aria-label="Business card back">
      <div class="brand">
        <span class="brand__mark" aria-hidden="true"></span>
        <div class="brand__name">BRAMBLE FIREARMS</div>
        <div class="brand__tagline">TRAINING AND CONSULTING</div>
      </div>
    </section>
  </main>
</body>
</html>
```